Update patient consent forms and contract

Objective
Redesign the existing patient contract information document to create a modern,contempory, and easy-to-understand experience for patients. The updated design should improve readability, accessibility, and overall presentation while maintaining compliance with healthcare and legal requirements.

Key Deliverables

Refreshed visual design and layout
Improved information hierarchy and readability
Modern typography and colour palette aligned with brand guidelines
Clear section headings and navigation
Print-ready and digital versions (PDF)

Include KEV Logo within patient KEV consent to treatment. Ideally this document should be portrait not landscape.
Updates

I would love a front page to be included in the document

```html
<!DOCTYPE html>
<html lang="en">
<head>
<meta charset="utf-8">
<title>Payment Option Selection – Lumen Orthodontics</title>
<link href="https://fonts.googleapis.com/css2?family=Outfit:wght@400;500;600;700&family=Roboto:wght@500&display=swap" rel="stylesheet">
<style>
  :root{
    --navy:#1f3556;
    --blue:#0b93d6;
    --icon:#7cc7ef;
    --ink:#1e1e1e;
    --rule:#c9c9c9;
    --grey:#9a9a9a;
    --backdrop:#e6e6e6;
    --paper:#ffffff;
  }
  *{margin:0;padding:0;box-sizing:border-box}
  html,body{width:1200px;height:943px;overflow:hidden}
  body{background:var(--backdrop);font-family:"Outfit",sans-serif;color:var(--ink)}
  .page{position:absolute;left:252px;top:21px;width:696px;height:900px;background:var(--paper);overflow:hidden}
  .page > *{position:absolute}

  .title{left:39px;top:30px;font-size:25px;font-weight:700;color:var(--navy);letter-spacing:-.2px}
  .brand{display:flex;align-items:center;gap:7px;font-size:15px;font-weight:500;color:var(--grey)}
  .brand-kev{left:364px;top:30px}
  .brand-kev .mark{width:28px;height:28px;border-radius:50%;border:5px solid var(--grey)}
  .brand-lumen{left:523px;top:30px}
  .brand-lumen .mark{width:26px;height:26px;border-radius:50%;background:var(--blue)}

  .thanks{left:40px;top:80px;font-size:12.5px;font-weight:600}
  .intro{left:40px;top:102px;width:620px;font-size:12.3px;line-height:20px}
  .rule{left:38px;width:620px;height:1px;background:var(--rule)}
  .rule-dashed{left:44px;width:608px;border-top:1px dashed var(--rule)}

  .section-head{left:25px;font-size:19px;font-weight:600;color:var(--blue);display:flex;align-items:center;gap:10px}
  .section-head::before{content:"";width:4px;height:4px;border-radius:50%;background:var(--blue)}
  .option{left:46px;display:flex;align-items:center;gap:10px;font-family:"Roboto",sans-serif;font-weight:500;font-size:13.5px;color:var(--navy)}
  .checkbox{width:21px;height:21px;border:2px solid var(--blue);border-radius:3px}
  .body-text{left:40px;width:605px;font-size:12px;line-height:16px}
  .icon{left:327px}

  .sign-line{top:730px;height:1px;width:116px;background:var(--ink)}
  .sign-label{top:734px;width:116px;text-align:center;font-size:13.5px;font-weight:600}

  .footer-rule{left:37px;top:772px;width:623px;height:1px;background:var(--rule)}
  .col-divider{top:776px;width:1px;height:108px;background:var(--rule)}

  .foot{top:781px;font-size:9.4px;line-height:19px}
  .foot h3{font-size:10px;font-weight:600;margin-bottom:1px}
  .foot ul{list-style:none}
  .foot-bank{left:40px}
  .foot-bank dl{display:grid;grid-template-columns:94px auto}
  .foot-bank dt{color:var(--blue);font-weight:600}
  .foot-bank dd{font-weight:600}
  .foot-info{left:246px}
  .foot-info li{display:flex;align-items:center;gap:7px}
  .foot-info svg{flex:none;width:11px}
  .foot-docs{left:477px}
  .foot-docs li{display:flex;align-items:flex-start;gap:6px;line-height:10px;margin-bottom:6px}
  .foot-docs svg{flex:none;margin-top:2px}
  .foot-docs strong{font-weight:600;display:block}
</style>
</head>
<body>
<main class="page">
  <h1 class="title">Payment Option Selection</h1>
  <div class="brand brand-kev"><span class="mark"></span>KEV</div>
  <div class="brand brand-lumen"><span class="mark"></span>lumen orthodontics</div>

  <p class="thanks">Thank you for choosing Lumen Orthodontics.</p>
  <p class="intro">To assist with managing your treatment fees, please select your preferred payment method below. If you would prefer to pay at each scheduled appointment, please advise our reception team. Please note that appointments are generally scheduled every 6–8 weeks.</p>
  <div class="rule" style="top:182px"></div>

  <h2 class="section-head" style="top:198px">Please select one option:</h2>

  <div class="option" style="top:238px"><span class="checkbox"></span>Credit Card Direct Debit</div>
  <p class="body-text" style="top:270px">I would like to pay via credit card direct debit.</p>
  <svg class="icon" style="top:245px" width="58" height="42" viewBox="0 0 58 42" fill="none" stroke="var(--icon)" stroke-width="1.6">
    <rect x="1" y="1" width="47" height="32" rx="3"/>
    <line x1="1" y1="19" x2="48" y2="19"/>
    <line x1="1" y1="24" x2="48" y2="24"/>
    <line x1="7" y1="8" x2="16" y2="8"/>
    <line x1="7" y1="12" x2="22" y2="12"/>
    <circle cx="47" cy="31" r="9" fill="#fff"/>
    <path d="M42 31h9M47.5 27.5l3.5 3.5-3.5 3.5"/>
  </svg>
  <p class="body-text" style="top:302px">I understand that Lumen Orthodontics will send me a secure PayLink payment link to enter my credit card details. The card provided will be securely stored and used as my nominated payment method for future scheduled payments relating to my treatment plan.</p>

  <div class="rule-dashed" style="top:365px"></div>

  <div class="option" style="top:384px"><span class="checkbox"></span>Monthly Direct Bank Transfer</div>
  <p class="body-text" style="top:417px">I would like to pay via monthly direct bank transfer.</p>
  <svg class="icon" style="top:386px" width="45" height="42" viewBox="0 0 45 42" fill="none" stroke="var(--icon)" stroke-width="1.6">
    <rect x="1" y="5" width="43" height="36" rx="5"/>
    <line x1="1" y1="14" x2="44" y2="14"/>
    <line x1="12" y1="1" x2="12" y2="9"/>
    <line x1="33" y1="1" x2="33" y2="9"/>
    <path d="M13 24h18l-4-3M32 31H14l4 3"/>
  </svg>
  <p class="body-text" style="top:449px">I understand that I am responsible for ensuring monthly payments are made on time in accordance with my agreed payment arrangement.</p>

  <div class="rule" style="top:504px"></div>

  <h2 class="section-head" style="top:519px">Important</h2>
  <p class="body-text" style="top:551px;width:575px">When making direct transfer payments, please use the <strong>patient's full name</strong> as the payment reference (for example: Mia Harlow), rather than the account holder's name. This ensures payments are correctly allocated to your treatment account.</p>

  <h2 class="section-head" style="top:613px">Patient Declaration</h2>
  <p class="body-text" style="top:644px">I have read and understood the payment options above and agree to my selected payment method.</p>

  <div class="sign-line" style="left:108px"></div>
  <div class="sign-label" style="left:108px">Signature</div>
  <div class="sign-line" style="left:472px"></div>
  <div class="sign-label" style="left:472px">Date</div>

  <div class="footer-rule"></div>
  <div class="col-divider" style="left:224px"></div>
  <div class="col-divider" style="left:452px"></div>

  <section class="foot foot-bank">
    <h3>Our bank account details:</h3>
    <dl>
      <dt>Account Name</dt><dd>: Lumen Orthodontics</dd>
      <dt>Bank</dt><dd>: Harbour Bank</dd>
      <dt>BSB</dt><dd>: 012 345</dd>
      <dt>Account Number</dt><dd>: 12345678</dd>
    </dl>
  </section>

  <section class="foot foot-info">
    <h3>Information:</h3>
    <ul>
      <li><svg height="11" viewBox="0 0 9 11" fill="none" stroke="var(--blue)"><path d="M4.5 10.5S1 6.5 1 4.2a3.5 3.5 0 017 0c0 2.3-3.5 6.3-3.5 6.3z"/><circle cx="4.5" cy="4.2" r="1.2"/></svg>48 Elmstead Rd, Kingsford VIC 3199</li>
      <li><svg height="10" viewBox="0 0 10 10" fill="none" stroke="var(--blue)"><path d="M2 1l2 2-1 1.5a6 6 0 002.5 2.5L7 6l2 2-1.5 1.5C4 9 1 6 .5 2.5z"/></svg>03 9000 1234</li>
      <li><svg height="10" viewBox="0 0 10 10" fill="none" stroke="var(--blue)"><rect x="1" y="3" width="8" height="6" rx="1"/><rect x="3" y="1" width="4" height="3"/></svg>03 9000 5678</li>
      <li><svg height="9" viewBox="0 0 11 9" fill="none" stroke="var(--blue)"><rect x="1" y="1" width="9" height="7"/><path d="M1 1l4.5 4L10 1"/></svg>hello@lumen-ortho.com.au</li>
    </ul>
  </section>

  <section class="foot foot-docs">
    <h3 style="margin-bottom:3px">Registered Specialist Orthodontists:</h3>
    <ul>
      <li><svg width="11" height="13" viewBox="0 0 11 13" fill="none" stroke="var(--icon)"><path d="M2 1c2 0 2 1 3.5 1S7 1 9 1s1.5 3 1 5-1 6-2 6-1-4-2.5-4S4 12 3 12 1 8 .5 6 0 1 2 1z"/></svg><span><strong>Dr Anna Fielding</strong>MDSc, Grad Dip Clin Dent, BDSc(Hons)</span></li>
      <li><svg width="11" height="13" viewBox="0 0 11 13" fill="none" stroke="var(--icon)"><path d="M2 1c2 0 2 1 3.5 1S7 1 9 1s1.5 3 1 5-1 6-2 6-1-4-2.5-4S4 12 3 12 1 8 .5 6 0 1 2 1z"/></svg><span><strong>Dr Paul Renner</strong>MDSc, Grad Dip Clin Dent, MOrth, BDSc</span></li>
      <li><svg width="11" height="13" viewBox="0 0 11 13" fill="none" stroke="var(--icon)"><path d="M2 1c2 0 2 1 3.5 1S7 1 9 1s1.5 3 1 5-1 6-2 6-1-4-2.5-4S4 12 3 12 1 8 .5 6 0 1 2 1z"/></svg><span><strong>Dr Lucas Ward</strong>DCD, MOrth, MRACDS (Orth), BDSc (Hons)</span></li>
    </ul>
  </section>
</main>
</body>
</html>
```